Layout for site fence advertising - length approx. 250 cm x 125 cm

The advertising will later be printed on a PVC film and used for events or on sports fields.

Main services :
Your regional contact at
Real estate and business financing
independent insurance advice

```html
<!DOCTYPE html>
<html lang="en">
<head>
<meta charset="utf-8">
<title>Rheinfeld Finanz – Fence Banner</title>
<link rel="stylesheet" href="https://fonts.googleapis.com/css2?family=Bebas+Neue&family=Poppins:wght@300;400;600;700&display=swap">
<style>
  :root {
    --page-bg: #e6e6e6;
    --brand-blue: #1f58c9;
    --brand-blue-light: #2b6fe0;
    --brand-blue-deep: #1848b0;
    --paper: #ffffff;
    --ink: #262626;
    --footer: #2a2a2a;
    --tag-grey: #6f6f6f;
  }
  html, body {
    margin: 0;
    padding: 0;
    width: 943px;
    height: 1200px;
    overflow: hidden;
    background: var(--page-bg);
  }
  .fence-banner {
    position: absolute;
    left: 40px;
    top: 385px;
    width: 863px;
    height: 430px;
    display: block;
    box-shadow: 0 10px 28px rgba(0, 0, 0, 0.28);
  }
  .headline { font-family: "Bebas Neue", "Oswald", sans-serif; }
  .brand-name { font-family: "Poppins", sans-serif; font-weight: 600; }
  .brand-tagline { font-family: "Poppins", sans-serif; font-weight: 400; }
  .contact-text { font-family: "Poppins", sans-serif; font-weight: 400; }
  .contact-tag-light { font-family: "Poppins", sans-serif; font-weight: 300; }
  .contact-tag-bold { font-family: "Poppins", sans-serif; font-weight: 700; }
</style>
</head>
<body>
<svg class="fence-banner" viewBox="0 0 1385 690" xmlns="http://www.w3.org/2000/svg">
  <defs>
    <linearGradient id="blueBand" x1="0" y1="0" x2="1" y2="1">
      <stop offset="0" stop-color="var(--brand-blue-deep)"/>
      <stop offset="0.6" stop-color="var(--brand-blue)"/>
      <stop offset="1" stop-color="var(--brand-blue-light)"/>
    </linearGradient>
    <linearGradient id="cityView" x1="0" y1="0" x2="0" y2="1">
      <stop offset="0" stop-color="#c9dcee"/>
      <stop offset="0.22" stop-color="#e9eef2"/>
      <stop offset="0.3" stop-color="#8e99a3"/>
      <stop offset="0.6" stop-color="#8a7e70"/>
      <stop offset="0.8" stop-color="#8e9a4e"/>
      <stop offset="1" stop-color="#4f6a34"/>
    </linearGradient>
    <linearGradient id="portraitTone" x1="0" y1="0" x2="0" y2="1">
      <stop offset="0" stop-color="#b99882"/>
      <stop offset="0.35" stop-color="#3a3640"/>
      <stop offset="1" stop-color="#24222a"/>
    </linearGradient>
  </defs>

  <!-- top white field -->
  <rect class="header-field" x="0" y="0" width="1385" height="545" fill="var(--paper)"/>

  <!-- city view photo area -->
  <rect class="city-photo" x="808" y="0" width="577" height="545" fill="url(#cityView)" role="img" aria-label="Photo: panoramic view over a city with river and vineyards"/>

  <!-- blue headline band with diagonal -->
  <polygon class="headline-band" points="0,166 640,166 803,0 808,0 808,545 0,545" fill="url(#blueBand)"/>

  <!-- advisor portrait cutout -->
  <path class="advisor-portrait" d="M738,545 L758,300 Q790,245 855,228 L862,150 Q868,62 930,62 Q992,62 998,150 L1004,228 Q1072,248 1090,305 L1100,545 Z" fill="url(#portraitTone)" stroke="var(--paper)" stroke-width="3" role="img" aria-label="Photo: portrait of the advisor in a dark suit"/>

  <!-- brand -->
  <circle class="brand-mark" cx="108" cy="91" r="52" fill="var(--brand-blue)"/>
  <line class="brand-divider" x1="180" y1="32" x2="180" y2="152" stroke="var(--ink)" stroke-width="3"/>
  <text class="brand-name" x="190" y="88" font-size="24" fill="var(--brand-blue)">Rheinfeld Finanz GmbH</text>
  <text class="brand-tagline" x="190" y="113" font-size="16" fill="var(--ink)">Finanzieren, Versichern, Vorsorgen</text>

  <!-- headline -->
  <text class="headline" x="45" y="318" font-size="152" fill="var(--paper)" textLength="648" lengthAdjust="spacingAndGlyphs">REAL ESTATE &amp;</text>
  <text class="headline" x="45" y="413" font-size="106" fill="var(--paper)" textLength="648" lengthAdjust="spacingAndGlyphs">BUSINESS FINANCING</text>

  <rect class="service-box" x="49" y="438" width="645" height="66" fill="var(--paper)"/>
  <text class="headline" x="68" y="495" font-size="64" fill="var(--ink)" textLength="606" lengthAdjust="spacingAndGlyphs">INDEPENDENT INSURANCE ADVICER</text>

  <!-- footer -->
  <rect class="footer-bar" x="0" y="553" width="1385" height="137" fill="var(--footer)"/>
  <polygon class="contact-tag" points="50,588 538,588 553,636 50,636" fill="var(--tag-grey)"/>
  <text x="68" y="625" font-size="29" fill="var(--paper)" textLength="450" lengthAdjust="spacingAndGlyphs"><tspan class="contact-tag-light">YOUR REGIONAL </tspan><tspan class="contact-tag-bold">CONTACT AT</tspan></text>
  <text class="contact-text" x="563" y="626" font-size="39" fill="var(--paper)" textLength="395" lengthAdjust="spacingAndGlyphs">www.rheinfeld-finanz.at</text>
  <line class="contact-divider" x1="981" y1="590" x2="981" y2="634" stroke="var(--paper)" stroke-width="2"/>
  <text class="contact-text" x="1003" y="626" font-size="39" fill="var(--paper)" textLength="338" lengthAdjust="spacingAndGlyphs">+43 660 214 5870</text>
</svg>
</body>
</html>
```